Copperleaf Roofing Business Card

This is my current business card. But I’d like to make some changes. Somewhere on the card I’d like to list some of the services we offer. Maybe on the back? But I’d still like to keep the red. White and black modern look.

-residential & commercial roofing
-Roof Repairs & Maintenance
-Storm Damage & Insurance Claims specialist
-Christmas Lights and permanent Christmas lights
Fencing. Windows. Gutters. Siding. Sheetrock, painting.

```html
<!DOCTYPE html>
<html lang="en">
<head>
<meta charset="utf-8">
<title>Copperleaf Roofing Co. – Business Card</title>
<link rel="stylesheet" href="https://fonts.googleapis.com/css2?family=Michroma&family=Open+Sans:wght@400;500&family=Roboto+Condensed:wght@400;600&display=swap">
<style>
  :root{
    --red:#d81f26;
    --red-dark:#6e0e10;
    --red-mid:#a3161a;
    --black:#111111;
    --white:#ffffff;
    --stage:#d4d5d7;
    --ink:#1a1a1a;
  }
  *{margin:0;padding:0;box-sizing:border-box}
  html,body{width:900px;height:1200px;overflow:hidden}
  body{background:var(--stage);position:relative;font-family:"Open Sans",sans-serif;color:var(--ink)}

  .card{position:absolute;left:136px;width:630px;border-radius:12px;overflow:hidden}
  .card-front{top:215px;height:357px}
  .card-back{top:628px;height:359px;background:var(--white)}

  .tartan-field{
    position:absolute;inset:0;
    background:
      linear-gradient(180deg,transparent 0 13%,var(--red) 13% 25%,rgba(255,255,255,.85) 25% 32%,var(--red) 32% 44%,var(--black) 44% 66%,var(--red) 66% 72%,transparent 72%),
      linear-gradient(90deg,var(--red-dark),var(--red-mid) 50%,var(--red-dark));
  }
  .front-mark{position:absolute;left:50%;top:50%;transform:translate(-50%,-50%);display:flex;flex-direction:column;align-items:center;gap:14px}
  .front-mark .dot{width:96px;height:96px;border-radius:50%;background:var(--red);border:4px solid var(--white)}
  .front-mark .brand{font-family:"Michroma",sans-serif;font-size:18px;color:var(--white);letter-spacing:1px;text-align:center;line-height:1.35}

  .back-brand{position:absolute;left:56px;top:52px;width:240px;display:flex;flex-direction:column;align-items:center}
  .back-brand .dot{width:86px;height:86px;border-radius:50%;background:var(--red)}
  .back-brand .brand{margin-top:14px;font-family:"Michroma",sans-serif;font-size:16px;line-height:1.45;color:var(--red);text-align:center;letter-spacing:.5px}

  .divider{position:absolute;left:293px;top:56px;width:1.5px;height:134px;background:var(--ink)}

  .contact{position:absolute;left:322px;top:56px}
  .contact .name{font-family:"Michroma",sans-serif;font-size:21px;letter-spacing:1px;color:var(--black);line-height:1.1}
  .contact .name .first{color:var(--red)}
  .contact .role{font-size:14px;letter-spacing:.5px;margin-top:6px}
  .contact ul{list-style:none;margin-top:16px}
  .contact li{display:flex;align-items:center;gap:6px;font-size:14.5px;letter-spacing:.6px;height:25px}
  .contact li.phone{letter-spacing:2.5px}
  .contact svg{width:14px;height:14px;flex:none}

  .services{position:absolute;left:0;right:0;top:225px;text-align:center;font-family:"Roboto Condensed",sans-serif}
  .services .heading{display:flex;align-items:center;justify-content:center;gap:10px;font-size:20px;font-weight:600;color:var(--red);letter-spacing:.5px}
  .services .heading::before,.services .heading::after{content:"";width:135px;height:1px;background:var(--ink)}
  .services p{font-size:14.5px;line-height:25px;color:var(--black)}
  .services .heading + p{margin-top:6px}
  .services .sep{color:var(--red);padding:0 3px}

  .tartan-strip{position:absolute;left:0;right:0;bottom:0;height:12px;background:linear-gradient(90deg,var(--red-dark),var(--red) 30%,var(--red-dark) 60%,var(--red) 85%,var(--red-dark))}
</style>
</head>
<body>

<section class="card card-front">
  <div class="tartan-field" role="img" aria-label="Red, black and white tartan plaid pattern"></div>
  <div class="front-mark">
    <span class="dot"></span>
    <span class="brand">COPPERLEAF<br>ROOFING CO.</span>
  </div>
</section>

<section class="card card-back">
  <div class="back-brand">
    <span class="dot"></span>
    <span class="brand">COPPERLEAF<br>ROOFING CO.</span>
  </div>

  <div class="divider"></div>

  <div class="contact">
    <h1 class="name"><span class="first">DALE</span> MERCER</h1>
    <p class="role">OWNER</p>
    <ul>
      <li class="phone">
        <svg viewBox="0 0 24 24"><path fill="#d81f26" d="M6.6 10.8a15.1 15.1 0 0 0 6.6 6.6l2.2-2.2a1 1 0 0 1 1-.25 11.4 11.4 0 0 0 3.6.57 1 1 0 0 1 1 1V20a1 1 0 0 1-1 1A17 17 0 0 1 3 4a1 1 0 0 1 1-1h3.5a1 1 0 0 1 1 1c0 1.25.2 2.45.57 3.57a1 1 0 0 1-.25 1z"/></svg>
        555-014-2288
      </li>
      <li>
        <svg viewBox="0 0 24 24"><rect x="2" y="5" width="20" height="14" fill="#d81f26"/><path d="M2 5l10 8 10-8" fill="none" stroke="#fff" stroke-width="1.6"/></svg>
        Dale@copperleafroofing.co
      </li>
      <li>
        <svg viewBox="0 0 24 24" fill="none" stroke="#d81f26" stroke-width="1.8"><circle cx="12" cy="12" r="9.5"/><ellipse cx="12" cy="12" rx="4" ry="9.5"/><path d="M2.5 12h19M4 7h16M4 17h16"/></svg>
        www.copperleafroofing.co
      </li>
    </ul>
  </div>

  <div class="services">
    <h2 class="heading">SERVICES WE OFFER</h2>
    <p>Residential &amp; Commercial Roofing <span class="sep">|</span> Roof Repairs &amp; Maintenance</p>
    <p>Storm Damage &amp; Insurance Claims specialist <span class="sep">|</span> Christmas Lights and permanent Christmas lights</p>
    <p>Fencing <span class="sep">|</span> Windows <span class="sep">|</span> Gutters <span class="sep">|</span> Siding <span class="sep">|</span> Sheetrock <span class="sep">|</span> Painting.</p>
  </div>

  <div class="tartan-strip" role="img" aria-label="Thin band of red, black and white tartan plaid"></div>
</section>

</body>
</html>
```